Update Powerpoint Presentation

We need to update the existing Powerpoint presentation to make it look more professional, less words and get the message across to potential clients. Our clients are banks and lenders in Australia.
Reason: To give the designers more time to come up with designs
Reason: I am looking for a design that is more innovative and doesn't just re-create what I gave. This presentation is only an example of what I would like I am keen to find a presentation that takes it to the next level.
It Professional

```html
<!DOCTYPE html>
<html lang="en">
<head>
<meta charset="utf-8">
<title>HLS – Presentation to XYZ Lender</title>
<link rel="stylesheet" href="https://fonts.googleapis.com/css2?family=PT+Sans:ital,wght@0,400;0,700;1,400&family=PT+Sans+Narrow:wght@400;700&family=EB+Garamond:ital,wght@1,700&display=swap">
<style>
:root{
  --navy:#27348b;
  --navy-dark:#1f2f86;
  --cyan:#2fb0e3;
  --cyan-light:#5cc3ea;
  --grey-panel:#e4e4e4;
  --grey-text:#777777;
  --ink:#222222;
  --paper:#ffffff;
  --backdrop:#e6e1d9;
  --map-land:#f3d2b0;
  --map-region:#b78ccc;
}
*{box-sizing:border-box;margin:0;padding:0}
html,body{width:1200px;height:600px;overflow:hidden;background:var(--backdrop)}
body{font-family:"PT Sans",Arial,sans-serif;color:var(--ink)}
.stage{position:absolute;left:0;top:0;width:1500px;height:750px;transform:scale(.8);transform-origin:0 0}
.slide{position:absolute;width:472px;height:354px;background:var(--paper);overflow:hidden;box-shadow:0 2px 6px rgba(0,0,0,.18)}
.slide--title{left:273px;top:8px}
.slide--messages{left:778px;top:8px}
.slide--intro{left:12px;top:382px}
.slide--services{left:517px;top:382px}
.slide--thanks{left:1012px;top:382px}

/* footer */
.slide-footer{position:absolute;left:0;right:0;bottom:0;height:19px;display:flex}
.page-no{width:32px;background:var(--cyan);color:#fff;font-size:9px;display:flex;align-items:center;justify-content:center}
.footer-bar{margin-left:12px;flex:1;background:var(--navy);color:#fff;display:flex;align-items:center;justify-content:space-between;padding:0 14px 0 64px}
.footer-bar .confidential{font-size:6.5px;letter-spacing:.1px}
.footer-bar .web{font-size:10px;letter-spacing:1.6px}

/* brand */
.brand{display:flex;flex-direction:column;align-items:center;color:var(--navy)}
.brand-mark{display:flex;align-items:center;gap:6px}
.brand-name{font-family:"PT Sans",Arial,sans-serif;font-weight:700;color:var(--navy);line-height:1}
.brand-dot{border-radius:50%;background:var(--cyan)}
.tagline{color:var(--navy);font-family:"PT Sans Narrow",Arial,sans-serif;white-space:nowrap}
.brand--large .brand-name{font-size:112px;letter-spacing:2px}
.brand--large .brand-dot{width:30px;height:30px}
.brand--large .tagline{font-size:19px;margin-top:-2px}
.brand--small{position:absolute;right:22px;top:10px}
.brand--small .brand-name{font-size:40px;letter-spacing:1px}
.brand--small .brand-dot{width:12px;height:12px}
.brand--small .tagline{font-size:7.5px}

/* heading tab */
.heading-tab{position:absolute;left:10px;top:28px;height:30px;padding:0 22px 0 12px;background:var(--navy);color:#fff;font-size:16px;display:flex;align-items:center;border-radius:0 4px 4px 0;clip-path:polygon(0 0,100% 0,100% 100%,14px 100%,0 82%)}
.tab-tail{position:absolute;top:28px;width:12px;height:30px;background:var(--navy);clip-path:polygon(0 0,100% 0,0 100%)}

/* slide 1 */
.slide--title .brand{position:absolute;left:0;right:0;top:34px}
.presentation-tab{position:absolute;left:155px;top:198px;height:28px;padding:0 12px;background:var(--navy);color:#fff;font-size:18px;display:flex;align-items:center;border-radius:3px}
.presentation-meta{position:absolute;left:0;right:0;top:246px;text-align:center;font-size:13px;line-height:27px}

/* slide 2 */
.message-label{position:absolute;left:12px;width:96px;background:var(--navy);color:#fff;font-size:9px;font-weight:700;text-align:center;display:flex;align-items:center;justify-content:center;line-height:1.25;clip-path:polygon(0 0,92% 0,100% 50%,92% 100%,0 100%)}
.message-box{position:absolute;left:123px;width:326px;background:var(--cyan-light);color:#fff;font-size:4.6px;line-height:1.32;padding:4px 7px;border-radius:4px}
.message-box p{margin-bottom:1px}
.message-box b{font-weight:700}

/* slide 3 */
.intro-title{position:absolute;top:84px;font-size:11px;font-weight:700}
.intro-panel{position:absolute;top:107px;height:214px;background:var(--navy);border-radius:3px}
.intro-panel--about{left:14px;width:216px;padding:8px 9px;color:#fff;font-size:6.2px;line-height:1.3}
.intro-panel--about p{margin-bottom:7px}
.intro-panel--offices{left:242px;width:215px;padding:8px}
.offices-map{width:100%;height:100%;border-radius:2px;background:linear-gradient(120deg,var(--map-land) 0%,var(--map-land) 45%,var(--map-region) 60%,#9f7fbf 100%)}

/* slide 4 */
.services-intro{position:absolute;left:16px;top:58px;width:440px;font-size:5.6px;line-height:1.35}
.services-intro p{margin-bottom:4px}
.service-side{position:absolute;left:17px;width:17px;background:var(--navy);color:#fff;border-radius:3px;display:flex;align-items:center;justify-content:center}
.service-side span{transform:rotate(-90deg);font-size:9px;font-style:italic;white-space:nowrap}
.service-steps{position:absolute;left:40px;height:26px;display:flex;gap:2px}
.service-step{background:var(--cyan);color:var(--navy);font-size:5.6px;font-style:italic;line-height:1.15;text-align:center;display:flex;align-items:center;justify-content:center;padding:0 4px;clip-path:polygon(0 0,calc(100% - 6px) 0,100% 100%,6px 100%)}
.service-step:first-child{clip-path:polygon(0 0,calc(100% - 6px) 0,100% 100%,0 100%)}
.service-step:last-child{clip-path:polygon(0 0,100% 0,100% 100%,6px 100%)}
.service-tasks{position:absolute;left:40px;right:18px;background:var(--grey-panel);border-radius:6px;display:flex;padding:4px 2px}
.service-tasks ul{font-size:4.8px;line-height:1.25;padding-left:8px}
.service-tasks li{margin-bottom:.5px}

/* slide 5 */
.slide--thanks .brand{position:absolute;left:0;right:0;top:34px}
.thanks-line{position:absolute;left:0;right:0;top:200px;text-align:center;font-family:"EB Garamond",Georgia,serif;font-style:italic;font-weight:700;color:var(--grey-text);font-size:24px;line-height:27px}
.contact{position:absolute;left:0;right:0;top:277px;text-align:center;font-size:10.5px;line-height:17px;color:#333}
</style>
</head>
<body>
<div class="stage">

  <!-- Slide 1 -->
  <section class="slide slide--title">
    <div class="brand brand--large">
      <div class="brand-mark"><span class="brand-name">HLS</span><span class="brand-dot"></span></div>
      <div class="tagline">Broad reach. Personal service.</div>
    </div>
    <div class="presentation-tab">PRESENTATION TO</div>
    <div class="presentation-meta"><div>XYZ Lender</div><div>June 2013</div></div>
    <footer class="slide-footer"><span class="page-no">1</span><div class="footer-bar"><span class="confidential">COMMERCIAL IN CONFIDENCE</span><span class="web">www.harbourline-ls.com</span></div></footer>
  </section>

  <!-- Slide 2 -->
  <section class="slide slide--messages">
    <h2 class="heading-tab">KEY MESSAGES</h2>
    <div class="brand brand--small">
      <div class="brand-mark"><span class="brand-name">HLS</span><span class="brand-dot"></span></div>
      <div class="tagline">Broad reach. Personal service.</div>
    </div>

    <div class="message-label" style="top:87px;height:17px">XYZ Lender</div>
    <div class="message-box" style="top:82px;height:27px"><p>XYZ Lender currently outsources Mortgage Processing of New Loans and Discharges to a third party. XYZ Lender is potentially looking to explore alternative models to enhance their existing service proposition through innovation and technology enhancements.</p></div>

    <div class="message-label" style="top:135px;height:17px">HLS</div>
    <div class="message-box" style="top:122px;height:44px"><p>HLS is the largest outsource mortgage document and settlement business in Australia. Its ultimate parent, Meridian Title Group, is a leading global provider of title insurance and settlement services for residential and commercial real estate transactions. With revenues of approximately $3.8 billion in 2012, the company offers its products and services directly and through its agents and partners throughout the United States and abroad.</p></div>

    <div class="message-label" style="top:205px;height:55px">Key<br>opportunities of<br>working with<br>HLS</div>
    <div class="message-box" style="top:180px;height:110px">
      <p><b>Refinances</b> – HLS currently undertakes the Switches processing for other clients and is achieving take up of between 50% and 70% with settlements occurring day 1 from documents being returned. We would like to discuss opportunities for us to undertake the refinance process on behalf of XYZ Lender and work with your clients to ensure the best possible uptake.</p>
      <p><b>Electronic Documents and Web Signing</b> – HLS has deployed this technology in New Zealand to allow the electronic delivery of documents and web signing and are in discussions with other lenders in Australia. HLS would like to work with XYZ Lender in establishing an Electronic Document delivery Solution.</p>
      <p><b>Discharges</b> – HLS would like to discuss the outsourcing of XYZ Lender's discharges to HLS. Relationship with the Third Party Channel – HLS has an exclusive relationship with the major aggregator groups and we understand their business and work closely with them by undertaking their own white label processing.</p>
      <p><b>ECNA</b> – HLS is working closely with ECNA to ensure a smooth transition from the existing manual processes to the new "Electronic World" of Conveyancing.</p>
    </div>

    <div class="message-label" style="top:302px;height:24px">Commitment<br>Sought</div>
    <div class="message-box" style="top:304px;height:20px"><p>HLS would like to work closely with XYZ Lender with a view to enhance XYZ Lender's end to end mortgage processing solution.</p></div>

    <footer class="slide-footer"><span class="page-no">2</span><div class="footer-bar"><span class="confidential">COMMERCIAL IN CONFIDENCE</span><span class="web">www.harbourline-ls.com</span></div></footer>
  </section>

  <!-- Slide 3 -->
  <section class="slide slide--intro">
    <h2 class="heading-tab">INTRODUCTION</h2>
    <div class="brand brand--small">
      <div class="brand-mark"><span class="brand-name">HLS</span><span class="brand-dot"></span></div>
      <div class="tagline">Broad reach. Personal service.</div>
    </div>
    <h3 class="intro-title" style="left:20px">ABOUT HARBOURLINE LOAN SERVICES</h3>
    <h3 class="intro-title" style="left:248px">HLS OFFICES</h3>
    <div class="intro-panel intro-panel--about">
      <p>Harbourline Loan Services (HLS) was established in NZ in 2001 and opened an office in Australia in 2004. In November 2007 HLS became a wholly owned subsidiary of Meridian Title Group and is the vehicle through which Meridian undertakes mortgage servicing in Australia and New Zealand.</p>
      <p>On 1 August 2012 HLS acquired Coastal Lenders Processing Services (CLPS) to form one of the largest mortgage processing companies in Australasia.</p>
      <p>In providing services to the mortgage industry, HLS utilizes and deploys its existing resources and capability as well as the resources available to it through the Meridian Title family of companies internationally.</p>
      <p>HLS have approximately 300 staff operating in offices in Sydney, Melbourne, Adelaide, Brisbane, Perth and Auckland, refer map opposite.</p>
      <p>HLS undertakes approximately 150,000 settlements p.a.</p>
    </div>
    <div class="intro-panel intro-panel--offices">
      <div class="offices-map" role="img" aria-label="Map of Australia and New Zealand marking the HLS offices and staff numbers in each city"></div>
    </div>
    <footer class="slide-footer"><span class="page-no">3</span><div class="footer-bar"><span class="confidential">COMMERCIAL IN CONFIDENCE</span><span class="web">www.harbourline-ls.com</span></div></footer>
  </section>

  <!-- Slide 4 -->
  <section class="slide slide--services">
    <h2 class="heading-tab">SERVICE OFFERINGS</h2>
    <div class="brand brand--small">
      <div class="brand-mark"><span class="brand-name">HLS</span><span class="brand-dot"></span></div>
      <div class="tagline">Broad reach. Personal service.</div>
    </div>
    <div class="services-intro">
      <p>"Mortgage Servicing" can mean different things in different jurisdictions. For the purpose of this document we use it to refer to the full range of mortgage management and administration services during the period from receipt of instructions to prepare documents until repayment and discharge of the mortgage that can be outsourced by the lender to a third party.</p>
      <p>The diagram below details the services provided by HLS.</p>
    </div>

    <div class="service-side" style="top:108px;height:110px"><span>New Loans</span></div>
    <div class="service-steps" style="top:111px;width:390px">
      <div class="service-step" style="width:60px">Document Preparation</div>
      <div class="service-step" style="width:54px">Verification</div>
      <div class="service-step" style="width:58px">Bookings And Enquiries</div>
      <div class="service-step" style="width:60px">Certification &amp; Settlement Preparation</div>
      <div class="service-step" style="width:54px">Settlements</div>
      <div class="service-step" style="width:54px">Stamping And Lodgement</div>
      <div class="service-step" style="width:42px">Custody</div>
    </div>
    <div class="service-tasks" style="top:140px;height:78px">
      <ul style="width:58px"><li>File creation</li><li>Complete / check title search</li><li>Check fees</li><li>Produce loan document pack</li><li>Forward documents to borrower</li></ul>
      <ul style="width:58px"><li>Verify that executed documents are completed correctly signed and witnessed</li><li>Follow up on incomplete documents</li></ul>
      <ul style="width:60px"><li>Contact the solicitor / conveyancer to book settlement</li><li>Contact outgoing lender to book settlement</li><li>Book settlement in settlement diary</li></ul>
      <ul style="width:58px"><li>Send certification document to lender and request funds</li><li>Confirm funds and disbursements required at settlement</li><li>Issue cheques</li></ul>
      <ul style="width:58px"><li>Complete final search</li><li>Collect bank cheques for settlement</li><li>Attend settlement</li><li>Confirm settlement and attend post settlement activities</li></ul>
      <ul style="width:58px"><li>Stamping of documents</li><li>Lodgement of the documents with the relevant LTO</li></ul>
      <ul style="width:56px"><li>Registered documents returned from LTO</li><li>Trail documents to the custodian</li></ul>
    </div>

    <div class="service-side" style="top:228px;height:97px"><span>Discharges</span></div>
    <div class="service-steps" style="top:224px;width:368px">
      <div class="service-step" style="width:62px">Document preparation</div>
      <div class="service-step" style="width:56px">Bookings and enquiries</div>
      <div class="service-step" style="width:60px">Advise payout figures</div>
      <div class="service-step" style="width:64px">Prepare settlement instructions</div>
      <div class="service-step" style="width:58px">Settlements</div>
      <div class="service-step" style="width:56px">Custody</div>
    </div>
    <div class="service-tasks" style="top:254px;height:68px">
      <ul style="width:62px"><li>File creation</li><li>Check fees</li><li>Produce discharge documents and arrange execution by attorney</li><li>Forward letter to requesting party</li></ul>
      <ul style="width:56px"><li>Book settlement in the settlement diary</li></ul>
      <ul style="width:62px"><li>Receive the payout figure from the outgoing lender</li><li>Advise payout figure and any fees to the incoming lender</li></ul>
      <ul style="width:64px"><li>Forward discharge documents and settlement instructions to effect settlement to applicable state office or settlement agent</li></ul>
      <ul style="width:58px"><li>Attend settlement and collect funds to payout loan</li><li>Deposit cheques</li></ul>
      <ul style="width:58px"><li>Trail any remaining documents from the security packet to the custodian</li></ul>
    </div>
    <footer class="slide-footer"><span class="page-no">4</span><div class="footer-bar"><span class="confidential">COMMERCIAL IN CONFIDENCE</span><span class="web">www.harbourline-ls.com</span></div></footer>
  </section>

  <!-- Slide 5 -->
  <section class="slide slide--thanks">
    <div class="brand brand--large">
      <div class="brand-mark"><span class="brand-name">HLS</span><span class="brand-dot"></span></div>
      <div class="tagline">Broad reach. Personal service.</div>
    </div>
    <div class="thanks-line">Thank You<br>For Your Attention</div>
    <div class="contact"><div>T: 123-456-0789</div><div>Street Name, City Name, State Zip Code</div></div>
    <footer class="slide-footer"><span class="page-no">5</span><div class="footer-bar"><span class="confidential">COMMERCIAL IN CONFIDENCE</span><span class="web">www.harbourline-ls.com</span></div></footer>
  </section>

</div>
</body>
</html>
```